New Business Card Design Project LORVANTI-Italy

we are LORVANTI-Italy
our company in the market for 3 years we are luxury cosmetic company and its about time for a facelift :)
i will like to have elegant luxurious and unique business card
that will give the person that get it a unique, luxurious and elegant impression
I'm VERY OPEN FOR NEW IDEAS , even duo i add a few files of things that i see on line and i like them

i add my logo as well
my website is LORVANTI.COM
(if you would like to see the main style that we have)

Target Market(s)

adult that have money :)

Industry/Entity Type

Business

Contact Information for Business Card

Name - Dario Lorvanti
Position - CEO and CO Founder
address - 4817 E Halvern
telephone - 555-384-1926
email - dario@lorvanti.com
fax - 555-384-1926
website - LORVANTI.COM

Colors
000000
959595
fbee3e
ffffff

Requirements
Must have
• big logo in GOLD color
• elegant look
• impressive
Nice to have
• not must but maybe classy pattern background
• not must but maybe emblem
• maybe clear plastic business card
Should not have
• colors
• images

```html
<!DOCTYPE html>
<html lang="en">
<head>
<meta charset="utf-8">
<title>LORVANTI Italy – Business Card</title>
<link rel="stylesheet" href="https://fonts.googleapis.com/css2?family=Tinos:wght@400;700&family=PT+Sans:wght@400&display=swap">
<style>
  :root {
    --page-bg: #ececec;
    --card-bg: #131313;
    --card-bg-deep: #0b0b0b;
    --gold: #e8be3f;
    --gold-line: #c9a233;
    --text-light: #e6e6e6;
    --pattern-tone: rgba(255,255,255,0.035);
  }
  * { margin: 0; padding: 0; box-sizing: border-box; }
  html, body { width: 1200px; height: 900px; overflow: hidden; }
  body {
    background: linear-gradient(180deg, #d9d9d9 0%, #f2f2f2 55%, #ffffff 100%);
    position: relative;
    font-family: "PT Sans", Arial, sans-serif;
  }
  .card {
    position: absolute;
    top: 184px;
    height: 490px;
    border-radius: 12px;
    background: radial-gradient(ellipse at 50% 35%, var(--card-bg) 0%, var(--card-bg-deep) 100%);
    overflow: hidden;
    text-align: center;
    color: var(--text-light);
  }
  .card--front { left: 299px; width: 301px; }
  .card--back { left: 645px; width: 304px; }

  .card__pattern {
    position: absolute;
    left: -60px; right: -60px; top: 140px; bottom: -80px;
    border-radius: 50%;
    background: radial-gradient(circle, transparent 52%, var(--pattern-tone) 56%, transparent 62%, var(--pattern-tone) 70%, transparent 78%);
  }

  .serif { font-family: "Tinos", "Times New Roman", serif; }

  .brand-name {
    position: absolute; left: 0; right: 0;
    color: var(--gold);
    font-family: "Tinos", "Times New Roman", serif;
    font-weight: 400;
  }
  .card--front .brand-name { top: 122px; font-size: 34px; letter-spacing: 2px; }
  .brand-circle {
    position: absolute;
    left: 50%;
    transform: translateX(-50%);
    border-radius: 50%;
    border: 3px solid var(--gold);
  }
  .card--front .brand-circle { top: 62px; width: 46px; height: 46px; }

  .person {
    position: absolute; left: 0; right: 0; top: 270px;
  }
  .person__name {
    font-family: "Tinos", "Times New Roman", serif;
    font-weight: 700;
    color: var(--gold);
    font-size: 19px;
    letter-spacing: 0.5px;
  }
  .person__role { font-size: 13.5px; margin-top: 2px; }

  .rule {
    height: 1px;
    width: 100px;
    margin: 0 auto;
    background: var(--gold-line);
  }
  .rule--top { margin-top: 12px; }
  .contact-icons {
    display: flex; justify-content: center; gap: 6px;
    margin-top: 13px;
  }
  .contact-icons svg { width: 16px; height: 16px; display: block; }
  .contact-list { list-style: none; margin-top: 9px; font-size: 14px; line-height: 17.5px; }
  .rule--bottom { margin-top: 12px; }
  .address { font-size: 14px; margin-top: 12px; }

  .card--back .brand-circle { top: 146px; width: 102px; height: 102px; }
  .card--back .brand-name { top: 264px; font-size: 44px; letter-spacing: 1px; line-height: 1; }
  .card--back .rule { position: absolute; top: 322px; left: 39px; width: 228px; height: 2px; margin: 0; }
  .card--back .region {
    position: absolute; left: 0; right: 0; top: 330px;
    color: var(--gold); font-size: 17px; letter-spacing: 1px;
  }
  .card--back .website {
    position: absolute; left: 0; right: 0; top: 430px;
    color: var(--gold); font-size: 16px; font-weight: 700; letter-spacing: 0.5px;
  }
</style>
</head>
<body>

<section class="card card--front" aria-label="Business card front">
  <div class="card__pattern" role="img" aria-label="Faint decorative pattern background"></div>
  <div class="brand-circle"></div>
  <div class="brand-name">LORVANTI</div>

  <div class="person">
    <div class="person__name">DARIO LORVANTI</div>
    <div class="person__role">CEO and CO Founder</div>
    <div class="rule rule--top"></div>
    <div class="contact-icons">
      <svg viewBox="0 0 16 16" aria-label="Telephone"><circle cx="8" cy="8" r="8" fill="#e8be3f"/><path d="M5 6.2c0-.8 1.3-1.4 3-1.4s3 .6 3 1.4l-.9.5-.4-.9H6.3l-.4.9zM5.6 7.6h4.8l.6 3.3H5z" fill="#131313"/></svg>
      <svg viewBox="0 0 16 16" aria-label="Fax"><circle cx="8" cy="8" r="8" fill="#e8be3f"/><path d="M5.8 4.5h3.6l.8.8v1.5H5.8zM4.8 7.3h6.4v4.2H4.8z" fill="#131313"/><rect x="6.3" y="8.4" width="3.4" height="1.6" fill="#e8be3f"/></svg>
      <svg viewBox="0 0 16 16" aria-label="Email"><circle cx="8" cy="8" r="8" fill="#e8be3f"/><rect x="4.5" y="5.5" width="7" height="5" fill="#131313"/><path d="M4.7 5.8 8 8.4l3.3-2.6" stroke="#e8be3f" stroke-width=".8" fill="none"/></svg>
    </div>
    <ul class="contact-list">
      <li>555-384-1926</li>
      <li>555-384-1926</li>
      <li>dario@lorvanti.com</li>
    </ul>
    <div class="rule rule--bottom"></div>
    <div class="address">4817 E Halvern</div>
  </div>
</section>

<section class="card card--back" aria-label="Business card back">
  <div class="card__pattern" role="img" aria-label="Faint decorative pattern background"></div>
  <div class="brand-circle"></div>
  <div class="brand-name">LORVANTI</div>
  <div class="rule"></div>
  <div class="region serif">ITALY</div>
  <div class="website serif">LORVANTI.COM</div>
</section>

</body>
</html>
```